Sonic Vale

Rebrand current website and move it to SonicVale.com. Looking for a professional, eye catching, top 10 in World type website. My current website is: https://madebytorven.sitepadhub.com/sonicvale
I would like it moved to sonicvale.com.

```html
<!DOCTYPE html>
<html lang="en">
<head>
<meta charset="utf-8">
<title>Sonic Vale</title>
<link href="https://fonts.googleapis.com/css2?family=Montserrat:wght@500;600;700&family=Roboto:wght@400;500;700&display=swap" rel="stylesheet">
<style>
:root{
  --blue:#2fa8e4;
  --bg:#050505;
  --panel:#0f0f10;
  --white:#ffffff;
  --grey:#9a9a9a;
  --dim:#555555;
  --head:"Montserrat",sans-serif;
  --body:"Roboto",sans-serif;
}
*{margin:0;padding:0;box-sizing:border-box}
html,body{width:1200px;height:4031px;overflow:hidden;background:var(--bg)}
body{position:relative;font-family:var(--body);color:var(--white)}
.abs{position:absolute}
.btn{position:absolute;display:flex;align-items:center;justify-content:center;gap:8px;background:var(--blue);color:var(--white);border-radius:30px;font:700 15px var(--body);text-transform:uppercase}
.btn .dot{width:14px;height:14px;border-radius:50%;background:var(--white);display:inline-flex;align-items:center;justify-content:center}
.btn .dot::after{content:"";border-left:5px solid var(--blue);border-top:3.5px solid transparent;border-bottom:3.5px solid transparent;margin-left:2px}
.heading{font:600 44px var(--head);letter-spacing:1px;text-transform:uppercase}
.heading .accent{color:var(--blue)}

/* header */
.topline{left:0;top:0;width:1200px;height:3px;background:var(--blue)}
.header{left:0;top:3px;width:1200px;height:120px;background:#000}
.logo{display:flex;align-items:center;gap:10px}
.logo .mark{width:16px;height:16px;border-radius:50%;background:var(--blue)}
.logo .name{font:700 30px var(--head);color:var(--blue);letter-spacing:1px}
.contact-item{display:flex;align-items:center;gap:14px}
.contact-item .ico{width:38px;height:38px;border-radius:50%;background:var(--white);display:flex;align-items:center;justify-content:center}
.contact-item small{display:block;font:400 12px var(--body);color:#bbb}
.contact-item b{font:700 15px var(--body)}
.contact-item b.big{font-size:20px}
.nav{left:422px;top:78px;width:778px;height:45px;background:var(--blue);clip-path:polygon(28px 0,100% 0,100% 100%,0 100%)}
.nav a{position:absolute;top:13px;font:500 15px var(--body);color:var(--white);text-decoration:none}

/* hero */
.hero-photo{left:0;top:123px;width:1200px;height:584px;background:radial-gradient(ellipse at 72% 40%,#6a6a6a 0,#3a3a3a 30%,#1a1a1a 65%,#0c0c0c 100%)}
.hero-title{left:112px;top:310px;font:700 46px var(--head);letter-spacing:1px}
.hero-text{left:112px;top:382px;font:500 16.5px/27px var(--body)}

/* about */
.about-shape{left:0;top:860px;width:422px;height:423px}
.about-photo{left:122px;top:783px;width:460px;height:410px;background:linear-gradient(135deg,#5a5068 0,#3a3440 45%,#d8d8d8 70%,#2a2a2a 100%)}
.about-kicker{left:648px;top:808px;font:600 21px var(--head);color:#bbb}
.about-name{left:646px;top:838px;font:700 44px var(--head);color:var(--blue);letter-spacing:1px}
.about-lead{left:644px;top:918px;width:440px;font:400 14px/26px var(--body);color:var(--dim)}
.about-body{left:644px;top:980px;width:445px;font:400 14px/26px var(--body);color:var(--grey)}

/* audio */
.audio-bg{left:0;top:1283px;width:1200px;height:688px;background:linear-gradient(180deg,#0b0b0b 0,#141414 45%,#1b1b1b 80%,#0d0d0d 100%)}
.track{position:absolute;width:468px;height:140px;border-radius:70px;background:var(--panel)}
.track .art{position:absolute;left:4px;top:4px;width:132px;height:132px;border-radius:50%}
.track .artist{position:absolute;left:168px;top:18px;font:400 15px var(--body);color:var(--grey)}
.track .title{position:absolute;left:168px;top:42px;font:700 16.5px var(--body)}
.track .price{position:absolute;left:168px;top:66px;font:700 13.5px var(--body);color:var(--blue)}
.track .player{position:absolute;left:158px;top:100px}

/* mixing */
.mix-title{left:110px;top:2092px;font:600 33px var(--head);color:#bbb;letter-spacing:1px}
.mix-sku{left:112px;top:2136px;font:400 13px var(--body);color:#ccc}
.mix-price{left:112px;top:2184px;font:700 19px var(--body);color:var(--blue)}
.mix-text{left:112px;top:2218px;font:400 16px/24px var(--body)}
.mix-side{left:590px;top:2057px;width:159px;height:333px;background:linear-gradient(90deg,#0a0a0a 0,#1c1c1c 60%,#151515 100%)}
.mix-photo{left:749px;top:2057px;width:339px;height:333px;background:linear-gradient(135deg,#d0307a 0,#5a3aa8 45%,#2a5ac8 100%)}

/* reviews */
.reviews-bg{left:0;top:2472px;width:1200px;height:391px;background:linear-gradient(180deg,#0b0b0b 0,#171717 50%,#0b0b0b 100%)}
.quote{left:0;width:1200px;text-align:center}

/* blog */
.post{position:absolute;top:3030px;width:310px;height:427px;border:2px solid #e6e6e6;background:var(--bg)}
.post .pic{position:absolute;left:0;top:0;width:306px;height:213px}
.post .date{position:absolute;right:0;top:188px;width:112px;height:25px;background:var(--blue);font:700 15px/25px var(--body);text-align:center;clip-path:polygon(10px 0,100% 0,100% 100%,0 100%)}
.post h3{position:absolute;left:16px;top:240px;width:280px;font:700 17px/25px var(--body)}
.post p{position:absolute;left:16px;top:300px;width:270px;font:400 13.5px/21px var(--body)}
.post .more{position:absolute;left:16px;top:388px;font:700 13.5px var(--body);color:var(--blue)}

/* footer */
.footer-bg{left:0;top:3560px;width:1200px;height:422px;background:linear-gradient(180deg,#0a0a0a,#121212)}
.info{position:absolute;top:3760px;width:300px;text-align:center}
.info .circ{width:74px;height:74px;border-radius:50%;background:var(--blue);margin:0 auto 30px;display:flex;align-items:center;justify-content:center}
.info h4{font:700 17px var(--body);margin-bottom:10px}
.info span{font:400 14.5px/22px var(--body)}
.copybar{left:0;top:3982px;width:1200px;height:49px;background:var(--blue)}
.copybar .txt{position:absolute;left:112px;top:16px;font:500 14.5px var(--body)}
.social{position:absolute;top:10px;width:31px;height:31px;border-radius:50%;border:1.5px solid var(--white)}
</style>
</head>
<body>

<!-- header -->
<div class="abs topline"></div>
<header class="abs header">
  <div class="abs logo" style="left:110px;top:34px"><span class="name">SONIC VALE</span><span class="mark"></span></div>
  <div class="abs contact-item" style="left:617px;top:17px">
    <div class="ico"><svg width="20" height="14" viewBox="0 0 20 14"><rect width="20" height="14" rx="2" fill="#2fa8e4"/><path d="M1 1l9 7 9-7" stroke="#fff" stroke-width="1.6" fill="none"/></svg></div>
    <div><small>Email Us On</small><b>hello@sonicvale.com</b></div>
  </div>
  <div class="abs contact-item" style="left:905px;top:17px">
    <div class="ico"><svg width="18" height="18" viewBox="0 0 24 24"><path d="M6.6 10.8a15 15 0 006.6 6.6l2.2-2.2c.3-.3.7-.4 1-.2 1.1.4 2.3.6 3.6.6.6 0 1 .4 1 1V20c0 .6-.4 1-1 1A17 17 0 013 4c0-.6.4-1 1-1h3.5c.6 0 1 .4 1 1 0 1.3.2 2.5.6 3.6.1.3 0 .7-.2 1z" fill="#2fa8e4"/></svg></div>
    <div><small>Call Us Today</small><b class="big">404-555-0182</b></div>
  </div>
</header>
<nav class="abs nav">
  <a style="left:36px">Home</a><a style="left:113px">About Me</a><a style="left:214px">Latest Audio</a>
  <a style="left:336px">Shop</a><a style="left:406px">Book Online</a><a style="left:524px">Blog</a><a style="left:590px">Contact Us</a>
</nav>

<!-- hero -->
<div class="abs hero-photo" role="img" aria-label="Black and white studio photo of a condenser microphone with pop filter over a mixing desk"></div>
<h1 class="abs hero-title">SONIC <span style="color:var(--blue)">VALE</span></h1>
<p class="abs hero-text">Intricate but gritty music producer who specializes<br>in all phases of music production.</p>
<div class="btn" style="left:112px;top:460px;width:237px;height:48px">Contact Us Today <span class="dot"></span></div>

<!-- about -->
<svg class="abs about-shape" viewBox="0 0 422 423"><polygon points="0,0 113,110 113,340 340,340 422,423 0,423" fill="#2fa8e4"/></svg>
<div class="abs about-photo" role="img" aria-label="Portrait of the producer in a white shirt in his home studio"></div>
<div class="abs about-kicker">ABOUT</div>
<h2 class="abs about-name">TORVEN MADDOX</h2>
<p class="abs about-lead">Hailing from New Orleans, Torven has always pushed himself to achieve more success in his music career.</p>
<p class="abs about-body">Looking to perfect his technical abilities and develop his own unique style, Torven draws upon his New Orleans roots and lifelong passion for music. Get in touch to learn more about his background, experience, and latest projects.</p>
<div class="btn" style="left:645px;top:1115px;width:180px;height:46px">Learn More <span class="dot"></span></div>

<!-- latest audio -->
<div class="abs audio-bg" role="img" aria-label="Dark background of a mixing console"></div>
<h2 class="abs heading" style="left:0;top:1360px;width:1200px;text-align:center"><span style="color:#bbb">LATEST</span> <span class="accent">AUDIO</span></h2>

<div class="track" style="left:112px;top:1460px">
  <div class="art" role="img" aria-label="Artist portrait" style="background:linear-gradient(135deg,#e0a060,#7a6ab0)"></div>
  <div class="artist">Torven</div><div class="title">OFF THE BLOCK (Remastered)</div><div class="price">Single $200.00</div>
  <svg class="player" width="290" height="26" viewBox="0 0 290 26"><path d="M10 13l6-4v8z" fill="#fff"/><rect x="22" y="9" width="8" height="8" fill="#fff"/><text x="36" y="8" font-size="9" fill="#fff" font-family="Roboto,sans-serif">Sound.mp3</text><text x="125" y="8" font-size="9" fill="#fff" font-family="Roboto,sans-serif">00:00/02:06</text><line x1="38" y1="16" x2="175" y2="16" stroke="#888" stroke-width="2"/><circle cx="38" cy="16" r="3.5" fill="#111" stroke="#fff"/><path d="M184 11h3l4-3v10l-4-3h-3z" fill="#fff"/><line x1="198" y1="13" x2="236" y2="13" stroke="#2fa8e4" stroke-width="3"/><circle cx="236" cy="13" r="3.5" fill="#111" stroke="#fff"/><path d="M250 10l3 3-3 3M258 10l-3 3 3 3" stroke="#fff" fill="none"/></svg>
</div>
<div class="track" style="left:620px;top:1460px">
  <div class="art" role="img" aria-label="Computer monitor showing a recording session" style="background:linear-gradient(135deg,#5078c0,#1a2030)"></div>
  <div class="artist">Torven</div><div class="title">OFF THE BLOCK (Remastered)</div><div class="price">Single $200.00</div>
  <svg class="player" width="290" height="26" viewBox="0 0 290 26"><path d="M10 13l6-4v8z" fill="#fff"/><rect x="22" y="9" width="8" height="8" fill="#fff"/><text x="36" y="8" font-size="9" fill="#fff" font-family="Roboto,sans-serif">Sound.mp3</text><text x="125" y="8" font-size="9" fill="#fff" font-family="Roboto,sans-serif">00:00/02:06</text><line x1="38" y1="16" x2="175" y2="16" stroke="#888" stroke-width="2"/><circle cx="38" cy="16" r="3.5" fill="#111" stroke="#fff"/><path d="M184 11h3l4-3v10l-4-3h-3z" fill="#fff"/><line x1="198" y1="13" x2="236" y2="13" stroke="#2fa8e4" stroke-width="3"/><circle cx="236" cy="13" r="3.5" fill="#111" stroke="#fff"/><path d="M250 10l3 3-3 3M258 10l-3 3 3 3" stroke="#fff" fill="none"/></svg>
</div>
<div class="track" style="left:112px;top:1650px">
  <div class="art" role="img" aria-label="Dim studio room with speakers" style="background:linear-gradient(135deg,#c8b890,#1a1a1a)"></div>
  <div class="artist">Torven</div><div class="title">OFF THE BLOCK (Remastered)</div><div class="price">Single $200.00</div>
  <svg class="player" width="290" height="26" viewBox="0 0 290 26"><path d="M10 13l6-4v8z" fill="#fff"/><rect x="22" y="9" width="8" height="8" fill="#fff"/><text x="36" y="8" font-size="9" fill="#fff" font-family="Roboto,sans-serif">Sound.mp3</text><text x="125" y="8" font-size="9" fill="#fff" font-family="Roboto,sans-serif">00:00/02:06</text><line x1="38" y1="16" x2="175" y2="16" stroke="#888" stroke-width="2"/><circle cx="38" cy="16" r="3.5" fill="#111" stroke="#fff"/><path d="M184 11h3l4-3v10l-4-3h-3z" fill="#fff"/><line x1="198" y1="13" x2="236" y2="13" stroke="#2fa8e4" stroke-width="3"/><circle cx="236" cy="13" r="3.5" fill="#111" stroke="#fff"/><path d="M250 10l3 3-3 3M258 10l-3 3 3 3" stroke="#fff" fill="none"/></svg>
</div>
<div class="track" style="left:620px;top:1650px">
  <div class="art" role="img" aria-label="Laptop and audio interface on a desk" style="background:linear-gradient(135deg,#e8e8e8,#a04020 60%,#2a1a10)"></div>
  <div class="artist">Torven</div><div class="title">OFF THE BLOCK (Remastered)</div><div class="price">Single $200.00</div>
  <svg class="player" width="290" height="26" viewBox="0 0 290 26"><path d="M10 13l6-4v8z" fill="#fff"/><rect x="22" y="9" width="8" height="8" fill="#fff"/><text x="36" y="8" font-size="9" fill="#fff" font-family="Roboto,sans-serif">Sound.mp3</text><text x="125" y="8" font-size="9" fill="#fff" font-family="Roboto,sans-serif">00:00/02:06</text><line x1="38" y1="16" x2="175" y2="16" stroke="#888" stroke-width="2"/><circle cx="38" cy="16" r="3.5" fill="#111" stroke="#fff"/><path d="M184 11h3l4-3v10l-4-3h-3z" fill="#fff"/><line x1="198" y1="13" x2="236" y2="13" stroke="#2fa8e4" stroke-width="3"/><circle cx="236" cy="13" r="3.5" fill="#111" stroke="#fff"/><path d="M250 10l3 3-3 3M258 10l-3 3 3 3" stroke="#fff" fill="none"/></svg>
</div>
<div class="btn" style="left:514px;top:1850px;width:172px;height:45px">Learn More <span class="dot"></span></div>

<!-- mixing -->
<h2 class="abs mix-title">MIXING AND <span style="color:var(--blue)">MASTERING</span></h2>
<div class="abs mix-sku">SKU: 364215376135191</div>
<div class="abs mix-price">$150.00</div>
<p class="abs mix-text">Get your music mix and mastered professionally to<br>industry standards.</p>
<div class="btn" style="left:112px;top:2298px;width:178px;height:49px">Shop Now <span class="dot"></span></div>
<div class="abs mix-side" role="img" aria-label="Black vinyl record partly hidden behind the photo"></div>
<div class="abs mix-photo" role="img" aria-label="Singer in headphones at a studio microphone under pink and blue light"></div>

<!-- reviews -->
<div class="abs reviews-bg" role="img" aria-label="Dark background of a mixing console"></div>
<h2 class="abs quote" style="top:2540px;font:600 37px var(--head);letter-spacing:1px">CLIENT <span style="color:var(--blue)">REVIEWS</span></h2>
<div class="abs quote" style="top:2615px;font:700 70px/70px Georgia,serif;color:var(--blue)">&ldquo;</div>
<p class="abs quote" style="top:2678px;font:700 20px/31px var(--body)">Music expresses that which cannot be said and on which it is<br>impossible to be silent</p>
<div class="abs quote" style="top:2758px;font:500 15px var(--body);color:var(--blue)">Marcel Dorne</div>

<!-- blog -->
<h2 class="abs quote" style="top:2946px;font:600 37px var(--head);letter-spacing:1px">LATEST <span style="color:var(--blue)">BLOG</span></h2>
<article class="post" style="left:110px">
  <div class="pic" role="img" aria-label="Musicians with a guitar and laptop" style="background:linear-gradient(135deg,#7a5030,#2a1a14 60%,#aaa)"></div>
  <div class="date">Jan 23, 2020</div>
  <h3>5 Things the Artist Needs to Know Before Recording</h3>
  <p>This is your blog post. Blogs are a great way to connect with your audience and keep them coming back.</p>
  <div class="more">READ MORE &raquo;</div>
</article>
<article class="post" style="left:445px">
  <div class="pic" role="img" aria-label="Headphones resting on a mixing desk" style="background:linear-gradient(135deg,#2a3a3a,#4a8a8a 50%,#101818)"></div>
  <div class="date">Jan 23, 2020</div>
  <h3>Recording Equipment Must-Haves for Every Studio</h3>
  <p>This is your blog post. Great looking images make your blog posts more visually compelling for your audience,</p>
  <div class="more">READ MORE &raquo;</div>
</article>
<article class="post" style="left:779px">
  <div class="pic" role="img" aria-label="Band rehearsing in a studio" style="background:linear-gradient(135deg,#6a4a3a,#2a2020 55%,#c0a030)"></div>
  <div class="date">Jan 23, 2020</div>
  <h3>Sound Check: Recording Tips from the Pros</h3>
  <p>This is your blog post. To really engage your site visitors we suggest you blog about subjects that are related</p>
  <div class="more">READ MORE &raquo;</div>
</article>

<!-- footer -->
<div class="abs footer-bg" role="img" aria-label="Dark background of a mixing console"></div>
<div class="abs logo" style="left:0;top:3648px;width:1200px;justify-content:center"><span class="name" style="font-size:38px">SONIC VALE</span><span class="mark" style="width:20px;height:20px"></span></div>
<div class="info" style="left:110px">
  <div class="circ"><svg width="26" height="26" viewBox="0 0 24 24"><path d="M6.6 10.8a15 15 0 006.6 6.6l2.2-2.2c.3-.3.7-.4 1-.2 1.1.4 2.3.6 3.6.6.6 0 1 .4 1 1V20c0 .6-.4 1-1 1A17 17 0 013 4c0-.6.4-1 1-1h3.5c.6 0 1 .4 1 1 0 1.3.2 2.5.6 3.6.1.3 0 .7-.2 1z" fill="#fff"/></svg></div>
  <h4>PHONE</h4><span>404-555-0182</span>
</div>
<div class="info" style="left:422px">
  <div class="circ"><svg width="28" height="20" viewBox="0 0 20 14"><rect width="20" height="14" rx="2" fill="#fff"/><path d="M1 1l9 7 9-7" stroke="#2fa8e4" stroke-width="1.6" fill="none"/></svg></div>
  <h4>Email</h4><span>hello@sonicvale.com</span>
</div>
<div class="info" style="left:778px">
  <div class="circ"><svg width="22" height="28" viewBox="0 0 22 28"><path d="M11 0a11 11 0 00-11 11c0 8 11 17 11 17s11-9 11-17A11 11 0 0011 0z" fill="#fff"/><circle cx="11" cy="11" r="4" fill="#2fa8e4"/></svg></div>
  <h4>Address</h4><span>Lorem ipsum dolor sit consectetur<br>adipiscing elit, sed do</span>
</div>
<div class="abs copybar">
  <div class="txt">Sonic Vale. Copyright 2021. ALL RIGHTS RESERVED.</div>
  <div class="social" style="left:969px" aria-label="Social profile"></div>
  <div class="social" style="left:1011px" aria-label="Social profile"></div>
  <div class="social" style="left:1054px" aria-label="Social profile"></div>
</div>

</body>
</html>
```